Upmarket Dessert Lounge needs a Business Card Design

We are an upmarket dessert lounge needing a business card to match our image.

We want something that is simple yet beautiful, feminine, classy, sophisticated and elegant. We want it to stand out and don't mind if it is bold.

The design should include our logo and colours of red or maroon with gold highlights. We don't mind if black is used.

Marlow & Quince

Target Market(s)

For those who like to indulge or treat themselves and give in to their temptations on good quality desserts.

Industry/Entity Type

Business

Requirements
Must have
• Must include our logo and our name

Marlow & Quince

M & Q

```html
<!DOCTYPE html>
<html lang="en">
<head>
<meta charset="utf-8">
<title>Marlow &amp; Quince — Business Card</title>
<link rel="stylesheet" href="https://fonts.googleapis.com/css2?family=Cinzel:wght@400&family=PT+Sans:wght@400;700&display=swap">
<style>
  :root {
    --maroon: #7a1416;
    --gold: #f7d7a6;
    --swoosh: #f3c68c;
    --paper: #ffffff;
    --backdrop: #ece8e3;
    --ink-light: #ffffff;
  }
  * { margin: 0; padding: 0; box-sizing: border-box; }
  html, body { width: 1200px; height: 402px; overflow: hidden; }
  body { background: var(--backdrop); position: relative; font-family: "PT Sans", sans-serif; }

  .card {
    position: absolute;
    top: 56px;
    width: 511px;
    height: 292px;
    overflow: hidden;
    box-shadow: 0 2px 6px rgba(0,0,0,0.18);
  }
  .card--front { left: 61px; background: var(--paper); }
  .card--back { left: 631px; background: var(--maroon); }

  .brand-name {
    position: absolute;
    left: 0; right: 0;
    top: 62px;
    text-align: center;
    font-family: "Cinzel", serif;
    font-weight: 400;
    font-size: 33px;
    letter-spacing: 1px;
    color: var(--maroon);
  }

  .person {
    position: absolute;
    left: 0; right: 0;
    top: 163px;
    text-align: center;
    color: var(--maroon);
    font-size: 18px;
    font-weight: 700;
  }
  .person__title { font-weight: 400; font-size: 14px; }

  .front-band { position: absolute; left: 0; top: 0; width: 511px; height: 292px; }

  .contact {
    position: absolute;
    left: 0; right: 0;
    text-align: center;
    color: var(--ink-light);
    font-size: 13.5px;
  }
  .contact--address { top: 226px; }
  .contact--lines { top: 255px; display: flex; justify-content: center; gap: 16px; align-items: center; }
  .contact--email { top: 273px; }
  .contact__item { display: inline-flex; align-items: center; gap: 3px; }
  .contact__icon { width: 11px; height: 11px; }

  .monogram {
    position: absolute;
    left: 0; right: 0;
    top: 88px;
    text-align: center;
    font-family: "Cinzel", serif;
    font-weight: 400;
    font-size: 92px;
    line-height: 1;
    color: var(--gold);
  }
</style>
</head>
<body>

<section class="card card--front">
  <svg class="front-band" viewBox="0 0 511 292" aria-hidden="true">
    <path d="M0 232 Q255 170 511 232 L511 236 Q255 182 0 236 Z" fill="var(--swoosh)"/>
    <path d="M0 244 Q255 192 511 244 L511 292 L0 292 Z" fill="var(--maroon)"/>
  </svg>

  <div class="brand-name">Marlow &amp; Quince</div>

  <p class="person">Your name, <span class="person__title">Title</span></p>

  <p class="contact contact--address">Street Name, City Name, State Zip Code</p>
  <p class="contact contact--lines">
    <span class="contact__item">
      <svg class="contact__icon" viewBox="0 0 12 12" aria-hidden="true"><circle cx="6" cy="6" r="5.3" fill="none" stroke="#fff" stroke-width="1"/><path d="M4 3.2 L5 3 L5.6 4.6 L5 5.1 Q5.6 6.6 6.9 7 L7.4 6.4 L9 7 L8.8 8 Q6 8.6 3.9 5.2 Z" fill="#fff"/></svg>
      555-014-2290
    </span>
    <span class="contact__item">
      <svg class="contact__icon" viewBox="0 0 12 12" aria-hidden="true"><rect x="3.2" y="0.8" width="5.6" height="10.4" rx="1" fill="none" stroke="#fff" stroke-width="1.1"/><rect x="4.3" y="2.2" width="3.4" height="5.6" fill="#fff"/></svg>
      555-014-2290
    </span>
    <span class="contact__item">
      <svg class="contact__icon" viewBox="0 0 12 12" aria-hidden="true"><g fill="none" stroke="#fff" stroke-width="1"><circle cx="6" cy="6" r="5.2"/><ellipse cx="6" cy="6" rx="2.3" ry="5.2"/><path d="M0.8 6 H11.2 M1.6 3.4 H10.4 M1.6 8.6 H10.4"/></g></svg>
      www.marlow&amp;quince.com
    </span>
  </p>
  <p class="contact contact--email">info@marlow&amp;quince.com</p>
</section>

<section class="card card--back">
  <div class="monogram">M&amp;Q</div>
</section>

</body>
</html>
```